Human Resource Consulting practice needs a business card design

We need a business card design (double sided colour) for our Human Resource (HR) consulting practice in regional New South Wales, australia. Our business name is Staff Compass. We support small and medium business across the Mid North Coast of New South Wales by providing them with outsourced HR support, services and products to help them achieve compliance with workplace legislation and across all areas of the employment lifecycle from recruitment to termination and everything in between. Our corporate colours are hot pink and black. The final design should communicate professionalism, trust, people focus.
I have attached the current (old) business card for your reference.

Target Market(s)

Business owners and high level managers

Industry/Entity Type

Business

Contact Information for Business Card

Name
Title
Phone no
Mobile no
Address
PO Box
email address
website

Colors
e34197

Requirements
Must have
• Tempate for changing business card personal details including Name, position title, mobile number, email address.
• Keep current logo and colours as per attached
• Logo must be presented in 2 colours or black only not white
Nice to have
• One side logo and graphic only other side logo and personal details
Should not have
• Should not be the same as the current version (attached) but a modern interpretation.
• Does not need a busy reverse side with our list of services as per current version. I feel this is too busy.
• No photos

```html
<!DOCTYPE html>
<html lang="en">
<head>
<meta charset="utf-8">
<title>Staff Compass – Business Card</title>
<link rel="stylesheet" href="https://fonts.googleapis.com/css2?family=Arimo:wght@400;700&display=swap">
<style>
  :root {
    --hot-pink: #e3127f;
    --pink-soft: #f07ab8;
    --ink: #1a1a1a;
    --charcoal: #2b2b2d;
    --card-white: #f6f6f6;
    --stage: #1c1c1e;
  }
  * { box-sizing: border-box; margin: 0; padding: 0; }
  html, body {
    width: 1200px; height: 873px; overflow: hidden;
    background: var(--stage);
    font-family: "Arimo", Arial, sans-serif;
  }
  .sheet {
    position: relative; width: 1200px; height: 873px;
    display: flex; align-items: center; justify-content: center; gap: 40px;
  }
  .card {
    position: relative; width: 540px; height: 330px; overflow: hidden;
    box-shadow: 0 12px 30px rgba(0,0,0,.5);
  }
  .wordmark {
    font-weight: 700; color: var(--hot-pink); white-space: nowrap;
    display: flex; align-items: center; gap: 10px;
  }
  .wordmark .dot { width: 10px; height: 10px; border-radius: 50%; background: var(--hot-pink); }

  /* Back side */
  .card--back { background: var(--charcoal); }
  .card--back .wordmark {
    position: absolute; left: 50%; top: 50%; transform: translate(-50%, -50%);
    font-size: 40px;
  }

  /* Front side */
  .card--front { background: linear-gradient(160deg, #ffffff 0%, var(--card-white) 60%, #e9e9e9 100%); }
  .card--front .wordmark {
    position: absolute; left: 34px; top: 140px; font-size: 30px;
  }
  .divider {
    position: absolute; left: 290px; top: 60px; width: 3px; height: 150px;
    background: linear-gradient(to bottom, rgba(227,18,127,0) 0%, var(--hot-pink) 30%, var(--hot-pink) 70%, rgba(227,18,127,0) 100%);
  }
  .person { position: absolute; left: 316px; top: 40px; }
  .person__name { font-size: 15px; font-weight: 700; color: var(--hot-pink); }
  .person__title { font-size: 11px; color: var(--ink); margin-top: 3px; }
  .contacts {
    position: absolute; left: 316px; top: 116px; list-style: none;
    font-size: 12px; color: var(--ink); line-height: 20px; letter-spacing: .3px;
  }
  .contacts b { display: inline-block; width: 22px; color: var(--hot-pink); }
  .website {
    position: absolute; left: 338px; top: 218px;
    font-size: 12px; color: var(--hot-pink); letter-spacing: .3px;
  }
  .rule { position: absolute; left: 0; right: 0; top: 250px; height: 6px; background: #3a3a3a; }
  .band {
    position: absolute; left: 0; right: 0; top: 256px; bottom: 0;
    background: var(--hot-pink);
    display: flex; align-items: center; padding-left: 34px;
  }
  .band__address { font-size: 14px; color: var(--pink-soft); letter-spacing: .6px; filter: brightness(1.25); }
</style>
</head>
<body>
  <main class="sheet">
    <section class="card card--back" aria-label="Card reverse">
      <div class="wordmark"><span class="dot"></span>Staff Compass</div>
    </section>

    <section class="card card--front" aria-label="Card front">
      <div class="wordmark"><span class="dot"></span>Staff Compass</div>
      <div class="divider"></div>
      <div class="person">
        <p class="person__name">Megan Hale</p>
        <p class="person__title">Principal Consultant</p>
      </div>
      <ul class="contacts">
        <li><b>T:</b>02 6550 4182</li>
        <li><b>M:</b>0411 362 905</li>
        <li><b>F:</b>02 6550 4183</li>
        <li><b>E:</b>megan@staffcompass.com.au</li>
      </ul>
      <p class="website">www.staffcompass.com.au</p>
      <div class="rule"></div>
      <div class="band"><p class="band__address">PO Box 318, Kendall Bay, NSW 2450</p></div>
    </section>
  </main>
</body>
</html>
```